Webshop Template

For our Webstore in UK we need a complete Template,
shoppingcart is Magento, the Shop is focussed on Download software,

the name: Kelvoramarket.co.uk

Check out some other good stores, like zandrilo.de
Updates

for example the Page from 

www.brunt.co.uk or

www.zandrilo.de

www.mokvelta.de

www.quarnepreis.de

The Logodesign which are in Consideration

http://www.plimvector.com/design/5520913/logo-design-by-tomek7ga

http://www.plimvector.com/design/5518207/logo-design-by-ivanoralba

http://www.plimvector.com/design/5517346/logo-design-by-granite-fables

http://www.plimvector.com/design/5516085/logo-design-by-quillotaste

http://www.plimvector.com/design/5515472/logo-design-by-tuvaro

http://www.plimvector.com/design/5514619/logo-design-by-lone-pine-graphic-

Target Market(s)

B2C - Consumer Marcet

Industry/Entity Type

Shop

```html
<!DOCTYPE html>
<html lang="en">
<head>
<meta charset="utf-8">
<title>Kelvoramarket.co.uk – Software Downloads</title>
<link href="https://fonts.googleapis.com/css2?family=Oswald:wght@400;500&family=Arimo:wght@400;700&display=swap" rel="stylesheet">
<style>
:root{
  --bg:#ebe4d8;
  --bar:#efe9df;
  --header:#f4f0ea;
  --pink:#e2737b;
  --pink-dark:#c9555f;
  --pink-light:#f0a1a6;
  --red:#b84a55;
  --green:#879a5b;
  --olive:#6a7a44;
  --price:#c24e5b;
  --caption:#d2a9a3;
  --text:#555;
  --muted:#8b8073;
  --line:#e6dccd;
  --panel:#f8f5f0;
  --white:#fff;
  --news:#d9cbb6;
}
*{box-sizing:border-box;margin:0;padding:0}
html,body{width:725px;height:1200px;overflow:hidden}
body{position:relative;background:var(--bg);font-family:Arimo,Arial,sans-serif;color:var(--text);font-size:7px}
.abs{position:absolute}
.topbar{left:0;top:0;width:725px;height:23px;background:var(--bar);border-bottom:1px solid #e2d8c8}
.account-links{left:87px;top:8px;font-size:6px;letter-spacing:.3px;color:#8a7d5d}
.account-links span{margin:0 4px;color:#b9ad97}
.search{left:498px;top:4px;width:138px;height:15px;background:var(--white);border:1px solid #d3c9b9}
.search p{position:absolute;left:4px;top:3px;font-size:6px;color:#aaa}
.search-btn{position:absolute;right:-1px;top:-1px;width:16px;height:15px;background:var(--olive)}
.header{left:0;top:23px;width:725px;height:73px;background:var(--header)}
.brand{left:83px;top:53px;font-family:Oswald,sans-serif;font-size:17px;font-weight:500;color:var(--pink)}
.phone-ico{left:404px;top:44px}
.contact-line{left:432px;top:48px;font-family:Oswald,sans-serif;font-size:9px;color:#444}
.contact-line small{display:block;font-family:Arimo,sans-serif;font-size:5px;color:#9a8560;margin-top:1px}
.divider-v{left:545px;top:48px;width:1px;height:20px;background:#ddd}
.truck{left:557px;top:48px;width:24px;height:17px;background:#c98a2a;border-radius:2px}
.shipping{left:587px;top:48px;font-family:Oswald,sans-serif;font-size:9px;color:#444}
.shipping small{display:block;font-family:Arimo,sans-serif;font-size:5px;color:#9a8560;margin-top:1px}
.nav{left:0;top:96px;width:725px;height:34px;background:linear-gradient(var(--pink-light),var(--pink) 45%,var(--pink-dark));border-bottom:4px solid #f3ece2}
.nav-item{position:absolute;top:10px;transform:translateX(-50%);font-family:Arimo,sans-serif;font-weight:700;font-size:8.5px;color:var(--white);white-space:nowrap}
.nav-sep{position:absolute;top:6px;width:1px;height:22px;background:rgba(255,255,255,.35)}
.box{background:var(--panel);border:1px solid #e9e0d2}
.shopby{left:82px;top:163px;width:169px;height:200px}
.shopby-inner{position:absolute;left:12px;top:11px;width:145px;height:177px;background:var(--white);border:1px solid var(--line)}
.shopby h2{font-family:Oswald,sans-serif;font-weight:400;font-size:11px;color:#333;padding:9px 0 10px 11px;border-bottom:1px solid var(--line);margin:0 4px}
.filter{padding:6px 0 0 11px}
.filter h3{font-size:6.5px;color:#222;margin-bottom:4px}
.filter a{display:block;font-size:6px;color:var(--pink-dark);text-decoration:none;line-height:10px}
.filter-sep{border-top:1px solid var(--line);margin:6px 4px 0}
.company a{line-height:14px}
.cart{left:82px;top:374px;width:169px;height:156px}
.cart-inner{position:absolute;left:12px;top:12px;width:145px;height:132px;background:var(--green);color:var(--white);border:2px solid #eef0e4}
.panel-title{font-family:Oswald,sans-serif;font-weight:400;font-size:11.5px;padding:7px 10px 6px;border-bottom:1px solid rgba(255,255,255,.25);margin:0 3px}
.cart-inner p{font-size:6px;padding:0 10px;line-height:11px}
.cart-inner p:first-of-type{margin-top:6px}
.cart-inner strong{font-weight:700}
.cart-thumb{position:absolute;left:11px;top:86px;width:28px;height:33px;background:linear-gradient(#3c5a2c,#99b25b);border:2px solid var(--white)}
.cart-item{position:absolute;left:45px;top:88px;font-size:6px;line-height:9px;width:68px}
.cart-actions{position:absolute;right:6px;top:90px;display:flex;gap:3px}
.cart-actions i{width:8px;height:8px;background:var(--white);display:block}
.compare{left:82px;top:542px;width:169px;height:136px}
.compare-inner{position:absolute;left:12px;top:12px;width:145px;height:113px;background:var(--red);color:var(--white);border:2px solid #f1e6e4}
.compare-row{display:flex;justify-content:space-between;align-items:center;font-size:6.5px;padding:6px 6px 6px 12px;border-bottom:1px solid rgba(255,255,255,.18)}
.compare-row i{width:8px;height:8px;background:var(--white);display:block}
.compare-foot{position:absolute;left:0;right:0;bottom:10px;padding:0 6px 0 11px;display:flex;justify-content:space-between;align-items:center;font-size:6px;font-weight:700;color:#3d1b1f}
.btn-light{background:#e6dcd0;color:#7a6d5f;font-family:Oswald,sans-serif;font-weight:400;font-size:6.5px;padding:4px 10px}
.tags{left:82px;top:691px;width:170px;display:flex;flex-wrap:wrap;gap:3px 2px}
.tags span{background:var(--white);border:1px solid var(--line);font-size:5.5px;color:#8a7f74;padding:4px 6px}
.all-tags{left:82px;top:765px;font-size:6px;color:var(--pink-dark);text-decoration:underline}
.main{left:269px;top:163px;width:373px;height:877px;background:var(--white);border:1px solid #e9e0d2}
.banner{left:281px;top:175px;width:349px;height:48px;border:1px solid #e6dccd;padding:3px}
.banner-fill{width:100%;height:100%;background:linear-gradient(90deg,#d9b7a4 0%,#a44650 25%,#9e3d48 100%)}
.toolbar{left:280px;width:351px;height:28px;background:var(--panel);border:1px solid var(--line);font-size:6px;color:#555}
.view-grid{position:absolute;left:8px;top:10px;width:7px;height:7px;background:linear-gradient(var(--pink-dark),var(--pink-dark)) 0 0/3px 3px no-repeat,linear-gradient(var(--pink-dark),var(--pink-dark)) 4px 0/3px 3px no-repeat,linear-gradient(var(--pink-dark),var(--pink-dark)) 0 4px/3px 3px no-repeat,linear-gradient(var(--pink-dark),var(--pink-dark)) 4px 4px/3px 3px no-repeat}
.view-sep{position:absolute;top:0;width:1px;height:26px;background:var(--line)}
.view-list{position:absolute;left:30px;top:10px;width:9px;height:7px;background:repeating-linear-gradient(#ccc 0 1px,transparent 1px 3px)}
.sort{position:absolute;left:53px;top:9px;display:flex;align-items:center;gap:3px}
.select{display:inline-block;border:1px solid #999;background:var(--white);height:10px;line-height:8px;padding:0 2px;position:relative}
.select::after{content:"";position:absolute;right:0;top:0;width:8px;height:8px;background:#ddd}
.pager{position:absolute;right:8px;top:9px;display:flex;align-items:center;gap:3px}
.pager a{color:var(--pink-dark);text-decoration:none}
.pager .cur{text-decoration:underline}
.card{position:absolute;width:170px;height:231px;background:var(--panel);border:1px solid var(--line)}
.card-img{position:absolute;left:12px;top:12px;width:146px;height:147px;background:var(--white);border:1px solid #ece4d8;display:flex;align-items:center;justify-content:center}
.card-img div{width:60px;height:60px;border-radius:50%}
.caption{position:absolute;left:0;right:0;top:164px;text-align:center;font-size:6.5px;color:var(--caption);padding-bottom:8px;margin:0 12px;border-bottom:1px solid var(--line)}
.price{position:absolute;left:12px;top:203px;font-family:Oswald,sans-serif;font-size:13px;color:var(--price)}
.add{position:absolute;left:110px;top:201px;width:48px;height:18px;background:var(--olive);color:var(--white);font-family:Oswald,sans-serif;font-size:6px;display:flex;align-items:center;justify-content:center;border:1px solid #55632f}
.footer{left:0;top:1051px;width:725px;height:117px;background:var(--white)}
.newsletter{left:82px;top:1062px;width:561px;height:33px;background:var(--news)}
.newsletter h4{position:absolute;left:10px;top:9px;font-family:Oswald,sans-serif;font-weight:400;font-size:10px;color:#7f7262}
.news-input{position:absolute;left:146px;top:6px;width:110px;height:22px;background:var(--white);border:1px solid #e0d6c6}
.news-btn{position:absolute;left:260px;top:6px;width:27px;height:22px;background:var(--pink-dark)}
.news-phone{position:absolute;left:385px;top:9px;font-family:Oswald,sans-serif;font-size:10px;color:#7f7262}
.foot-col{top:1106px;width:108px}
.foot-col a{display:block;font-size:6px;color:var(--pink-dark);text-decoration:none;line-height:15px;border-bottom:1px dotted #ddd}
.cards{left:514px;top:1109px;display:flex;gap:2px}
.cards span{width:22px;height:13px;border:1px solid #bbb;background:#f2f2f2}
.cards span:nth-child(1){background:#2a2f4a}
.cards span:nth-child(2){background:#4b87c4}
.cards span:nth-child(3){background:#f4f4f8}
.cards span:nth-child(4){background:#ececec}
.cards span:nth-child(5){background:#eef2f7}
.copyright{left:0;top:1168px;width:725px;height:32px;background:#efe9e1}
.copyright p{position:absolute;left:80px;top:15px;font-size:5.5px;color:#9c9288}
</style>
</head>
<body>
<div class="abs topbar"></div>
<div class="abs account-links">MY ACCOUNT<span>|</span>MY WISHLIST<span>|</span>MY CART<span>|</span>CHECKOUT<span>|</span>LOG IN</div>
<div class="abs search"><p>Search entire store here...</p><div class="search-btn">
<svg width="16" height="15" viewBox="0 0 16 15"><circle cx="7" cy="7" r="3" fill="none" stroke="#fff" stroke-width="1.3"/><line x1="9.2" y1="9.2" x2="11.5" y2="11.5" stroke="#fff" stroke-width="1.5"/></svg></div></div>

<div class="abs header"></div>
<div class="abs brand">Kelvoramarket.co.uk</div>
<svg class="abs phone-ico" width="26" height="28" viewBox="0 0 26 28"><path d="M4 14a9 9 0 0 1 18 0" fill="none" stroke="#444" stroke-width="2.5"/><rect x="2" y="13" width="5" height="9" rx="2" fill="#333"/><rect x="19" y="13" width="5" height="9" rx="2" fill="#333"/><path d="M21 22q0 4-6 4" fill="none" stroke="#444" stroke-width="1.2"/></svg>
<div class="abs contact-line">+444 (2000) 654321<small>Monday to Saturday: 10:00am - 7:00pm</small></div>
<div class="abs divider-v"></div>
<div class="abs truck"></div>
<div class="abs shipping">FREE SHIPPING<small>On Order Over $99.00</small></div>

<nav class="abs nav">
  <span class="nav-item" style="left:113px">HOME</span>
  <span class="nav-sep" style="left:173px"></span>
  <span class="nav-item" style="left:227px">Top 10 Apps</span>
  <span class="nav-sep" style="left:271px"></span>
  <span class="nav-item" style="left:321px">Freeware</span>
  <span class="nav-sep" style="left:368px"></span>
  <span class="nav-item" style="left:409px">Mobile Apps</span>
  <span class="nav-sep" style="left:460px"></span>
  <span class="nav-item" style="left:515px">Most Downloaded</span>
  <span class="nav-sep" style="left:568px"></span>
  <span class="nav-item" style="left:612px">Contact Us</span>
</nav>

<aside class="abs box shopby">
  <div class="shopby-inner">
    <h2>SHOP BY</h2>
    <div class="filter">
      <h3>Price</h3>
      <a>$100.00 - $200.00 (08)</a><a>$300.00 - $400.00 (12)</a><a>$400.00 - $500.00 (08)</a>
    </div>
    <div class="filter-sep"></div>
    <div class="filter company">
      <h3>Company</h3>
      <a>Norvane</a><a>Qelto</a><a>BRIMSOFT</a><a>PELLARO</a>
    </div>
  </div>
</aside>

<aside class="abs box cart">
  <div class="cart-inner">
    <div class="panel-title">MY CART</div>
    <p>There is <strong><u>1 item</u></strong> in your cart.</p>
    <p>Cart Subtotal: <strong>$152.98</strong></p>
    <p><strong>Recently added item(s)</strong></p>
    <div class="cart-thumb" role="img" aria-label="Product box thumbnail"></div>
    <div class="cart-item">Duis in ante sit amet sapien<br>1 x $649.99</div>
    <div class="cart-actions"><i></i><i></i></div>
  </div>
</aside>

<aside class="abs box compare">
  <div class="compare-inner">
    <div class="panel-title">COMPARE PRODUCTS</div>
    <div class="compare-row">Glasspane 8<i></i></div>
    <div class="compare-row">Glasspane 7 OEM<i></i></div>
    <div class="compare-foot">Clear All<span class="btn-light">COMPARE</span></div>
  </div>
</aside>

<div class="abs tags">
  <span>Camera</span><span>Hohoho</span><span>SEXY</span><span>Test</span><span>bones</span>
  <span>cool</span><span>Cool t-shirt</span><span>crap</span><span>good</span><span>green</span>
  <span>hip</span><span>laptop</span><span>mobile</span><span>nice</span><span>notebook</span>
  <span>phone</span><span>red</span><span>tight</span><span>tendy</span><span>young</span>
</div>
<a class="abs all-tags">View All Tags</a>

<main class="abs main"></main>
<div class="abs banner"><div class="banner-fill" role="img" aria-label="Special offer banner: discount up to 50%"></div></div>

<div class="abs toolbar" style="top:236px">
  <span class="view-grid"></span><span class="view-sep" style="left:22px"></span><span class="view-list"></span><span class="view-sep" style="left:46px"></span>
  <div class="sort">Sort By <span class="select" style="width:60px">Position</span><span style="color:var(--pink-dark)">↑</span></div>
  <div class="pager">Page: <a class="cur">1</a><a>2</a><a>3</a><a>›</a>&nbsp; Show <span class="select" style="width:22px">9</span> per page</div>
</div>

<section>
  <div class="card" style="left:280px;top:275px"><div class="card-img"><div role="img" aria-label="Browser app icon" style="background:radial-gradient(#f4a23a,#d9461c)"></div></div><p class="caption">Dolor sit amet conse ctetur adipisicing</p><span class="price">$651.00</span><span class="add">ADD TO CART</span></div>
  <div class="card" style="left:461px;top:275px"><div class="card-img"><div role="img" aria-label="Media player app icon" style="background:radial-gradient(#6fe27a,#1b3a22)"></div></div><p class="caption">Dolor sit amet conse ctetur adipisicing</p><span class="price">$651.00</span><span class="add">ADD TO CART</span></div>
  <div class="card" style="left:280px;top:517px"><div class="card-img"><div role="img" aria-label="Office app icon" style="background:radial-gradient(#e0453c,#8e1a18)"></div></div><p class="caption">Dolor sit amet conse ctetur adipisicing</p><span class="price">$651.00</span><span class="add">ADD TO CART</span></div>
  <div class="card" style="left:461px;top:517px"><div class="card-img"><div role="img" aria-label="Security app icon" style="background:radial-gradient(#e64b3d,#777)"></div></div><p class="caption">Dolor sit amet conse ctetur adipisicing</p><span class="price">$651.00</span><span class="add">ADD TO CART</span></div>
  <div class="card" style="left:280px;top:759px"><div class="card-img"><div role="img" aria-label="Messenger app icon" style="background:radial-gradient(#5fcfd8,#3b8a3a)"></div></div><p class="caption">Dolor sit amet conse ctetur adipisicing</p><span class="price">$651.00</span><span class="add">ADD TO CART</span></div>
  <div class="card" style="left:461px;top:759px"><div class="card-img"><div role="img" aria-label="Audio player app icon" style="background:radial-gradient(#f29a2e,#555)"></div></div><p class="caption">Dolor sit amet conse ctetur adipisicing</p><span class="price">$651.00</span><span class="add">ADD TO CART</span></div>
</section>

<div class="abs toolbar" style="top:1001px">
  <span class="view-grid"></span><span class="view-sep" style="left:22px"></span><span class="view-list"></span><span class="view-sep" style="left:46px"></span>
  <div class="sort">Sort By <span class="select" style="width:60px">Position</span><span style="color:var(--pink-dark)">↑</span></div>
  <div class="pager">Page: <a class="cur">1</a><a>2</a><a>3</a><a>›</a>&nbsp; Show <span class="select" style="width:22px">9</span> per page</div>
</div>

<footer class="abs footer"></footer>
<div class="abs newsletter">
  <h4>SIGN UP FOR OUR NEWSLETTER</h4>
  <div class="news-input"></div>
  <div class="news-btn"><svg width="27" height="22" viewBox="0 0 27 22"><rect x="7" y="6" width="13" height="10" fill="none" stroke="#fff" stroke-width="1.2"/><path d="M7 6l6.5 5.5L20 6" fill="none" stroke="#fff" stroke-width="1.2"/></svg></div>
  <span class="news-phone">+444 (2000) 654321</span>
</div>
<div class="abs foot-col" style="left:83px"><a>About US</a><a>Returns policy</a><a>Customer Support</a></div>
<div class="abs foot-col" style="left:234px"><a>Returns policy</a><a>Terms and conditions</a><a>Seecurity &amp; privacy</a></div>
<div class="abs foot-col" style="left:384px"><a>Circlebook</a><a>Chirpline</a><a>Vidstream</a></div>
<div class="abs cards"><span></span><span></span><span></span><span></span><span></span></div>
<div class="abs copyright"><p>Demo Store. All Rights Reserved</p></div>
</body>
</html>
```